Business Card Design (NEW FILES)

ATTENTION: New vector files are available. Please update your design to reflect/use the new (better resolution) logo images.

Seeking a unique and professional business card design for a commercial drone photography/videography business. The layout should feature
the logo (attached) and include the following information:
Owen Tarrick
614-502-7738
www.skylarkreelworks.example
NRD Certified Remote Pilot

Owen Tarrick

```html
<!DOCTYPE html>
<html lang="en">
<head>
<meta charset="utf-8">
<title>Skylark Reelworks – Business Card</title>
<link href="https://fonts.googleapis.com/css2?family=Montserrat:wght@700;800&family=Open+Sans:wght@400;600&display=swap" rel="stylesheet">
<style>
  :root {
    --navy: #1b1c4f;
    --navy-soft: #2e2f68;
    --orange: #e8894f;
    --orange-deep: #d97a3f;
    --white: #ffffff;
    --stage: #232323;
    --ink: #1b1c4f;
  }
  * { box-sizing: border-box; margin: 0; padding: 0; }
  html, body { width: 1200px; height: 780px; overflow: hidden; background: var(--stage); }
  .canvas { position: relative; width: 1200px; height: 780px; }

  .card {
    position: absolute;
    width: 520px; height: 300px;
    border-radius: 18px;
    overflow: hidden;
    top: 240px;
  }

  /* Front */
  .card-front { left: 50px; background: var(--white); font-family: "Open Sans", sans-serif; }
  .brand {
    position: absolute; left: 40px; top: 58px;
    display: flex; align-items: center; gap: 12px;
  }
  .brand-dot { width: 18px; height: 18px; border-radius: 50%; background: var(--orange); flex: none; }
  .brand-name {
    font-family: "Open Sans", sans-serif; font-weight: 600;
    font-size: 26px; color: var(--navy); letter-spacing: 0.5px; line-height: 1.1;
  }
  .divider { position: absolute; left: 0; top: 0; }
  .person { position: absolute; left: 288px; top: 64px; }
  .person-name {
    font-family: "Montserrat", sans-serif; font-weight: 800; font-size: 27px; line-height: 1;
    white-space: nowrap;
  }
  .person-name .first { color: var(--orange); }
  .person-name .last { color: var(--navy); }
  .person-role { font-size: 14px; font-weight: 600; color: var(--navy); margin-top: 5px; }
  .contacts { list-style: none; margin-top: 16px; }
  .contacts li {
    display: flex; align-items: center; gap: 8px;
    font-size: 12.5px; color: var(--ink); margin-bottom: 5px; white-space: nowrap;
  }
  .contacts svg { width: 13px; height: 13px; flex: none; }

  .credential-band {
    position: absolute; left: 0; bottom: 0; width: 370px; height: 36px;
    background: var(--navy); color: var(--white);
    font-size: 14px; line-height: 36px; padding-left: 34px; white-space: nowrap;
  }
  .drone-art {
    position: absolute; left: 370px; bottom: 0; width: 95px; height: 64px;
    border-radius: 12px 12px 0 0;
    background: linear-gradient(135deg, var(--navy), var(--navy-soft));
  }
  .corner-block {
    position: absolute; right: 0; bottom: 0; width: 55px; height: 36px;
    background: var(--orange);
  }

  /* Back */
  .card-back { left: 630px; background: var(--orange); }
  .back-pattern {
    position: absolute; inset: 0;
    background: linear-gradient(135deg, var(--orange), var(--orange-deep));
  }
  .back-brand {
    position: absolute; right: 90px; bottom: 42px;
    display: flex; align-items: center; gap: 8px;
  }
  .back-brand .brand-name { font-size: 17px; }
  .back-brand .brand-dot { width: 12px; height: 12px; background: var(--navy); }
</style>
</head>
<body>
<main class="canvas">

  <section class="card card-front" aria-label="Business card front">
    <div class="brand">
      <span class="brand-dot"></span>
      <span class="brand-name">Skylark<br>Reelworks</span>
    </div>

    <svg class="divider" width="520" height="300" aria-hidden="true">
      <line x1="272" y1="50" x2="238" y2="235" stroke="var(--orange)" stroke-width="1.2"/>
    </svg>

    <div class="person">
      <p class="person-name"><span class="first">Owen</span> <span class="last">Tarrick</span></p>
      <p class="person-role">Owner</p>
      <ul class="contacts">
        <li>
          <svg viewBox="0 0 16 16" aria-hidden="true"><path fill="var(--orange)" d="M3.6 1.5l2.3 2.7-1.3 1.6c.8 1.9 2.2 3.3 4.1 4.1l1.6-1.3 2.7 2.3-1.4 2.3C7 13.2 2.8 9 2.6 3.2z"/></svg>
          614-502-7738
        </li>
        <li>
          <svg viewBox="0 0 16 16" aria-hidden="true"><circle cx="8" cy="8" r="6.5" fill="none" stroke="var(--orange)" stroke-width="1.6"/><path d="M1.5 8h13M8 1.5c-3 3.5-3 9.5 0 13M8 1.5c3 3.5 3 9.5 0 13" fill="none" stroke="var(--orange)" stroke-width="1.2"/></svg>
          www.skylarkreelworks.example
        </li>
        <li>
          <svg viewBox="0 0 16 16" aria-hidden="true"><rect x="1.5" y="3.5" width="13" height="9" rx="1" fill="var(--orange)"/><path d="M1.8 4l6.2 5 6.2-5" fill="none" stroke="var(--white)" stroke-width="1.2"/></svg>
          info@skylarkreelworks.example
        </li>
      </ul>
    </div>

    <div class="credential-band">NRD Certified Remote Pilot, Fully Insured</div>
    <div class="drone-art" role="img" aria-label="Illustration of a camera drone in flight"></div>
    <div class="corner-block"></div>
  </section>

  <section class="card card-back" aria-label="Business card back">
    <div class="back-pattern" role="img" aria-label="Repeating pattern of small embossed drones"></div>
    <div class="back-brand">
      <span class="brand-dot"></span>
      <span class="brand-name">Skylark Reelworks</span>
    </div>
  </section>

</main>
</body>
</html>
```